We need a business card for our gym. We are a PowerCore affiliate in Decatur Georgie established 2008. Our company name is Rally Functional Fitness. PowerCore Building Prime Fitness. Instagram and website is @rallygym. Hashtags we use #rallywithheart #madetorally We want something similar to the the black and neon green design attached but a different color scheme. No neon colors. Are company colors are the same as the blue and white card attached. We are open to ideas as far as colors however - just no neon.

Contact Information for Business Card

Rally Functional Fitness
472 Halvern Drive
Fernvale WK 30041
Phone 404.555.0187 Website www.rallygym.example

Font styles to use
Other font styles liked:
• Futura Extra Bold Condensed

Colors

Designer to choose colors to be used in the design.

Requirements
Must have
• Our primary font we typically use for our name is Futura Extra Bold Condensed
Nice to have
• I attached a card from that is black and neon green from Zorva that we would like something similar. The blue and white is more similar to our colors. We also use have used black and white in the past. We use the chevrons as out logo. We are a PowerCore affiliate so I included a logo from them as well that may or may not be used on the card. Our instagram is @rallygym hashtags #madetorally #rallywithheart
Should not have
• No neon colors

```html
<!DOCTYPE html>
<html lang="en">
<head>
<meta charset="utf-8">
<title>Rally Functional Fitness – Business Card</title>
<link rel="stylesheet" href="https://fonts.googleapis.com/css2?family=Oswald:wght@700&family=Mulish:wght@400&display=swap">
<style>
  :root {
    --brand-teal: #2f8bab;
    --brand-teal-deep: #267a98;
    --brand-teal-light: #3a9cbd;
    --card-white: #ffffff;
    --ink-grey: #4a4f55;
    --backdrop: #2b2e33;
  }
  * { box-sizing: border-box; margin: 0; padding: 0; }
  html, body {
    width: 1200px; height: 900px; overflow: hidden;
    background: var(--backdrop);
  }
  .sheet {
    width: 1200px; height: 900px;
    display: flex; align-items: center; justify-content: center; gap: 40px;
  }
  .card {
    position: relative; border-radius: 4px; overflow: hidden;
    box-shadow: 0 14px 30px rgba(0,0,0,.45);
  }
  .brand-name {
    font-family: "Oswald", sans-serif; font-weight: 700;
    text-transform: uppercase; letter-spacing: .5px; line-height: 1.05;
  }

  /* Front – portrait */
  .card-front { width: 400px; height: 700px; background: var(--card-white); }
  .front-brand {
    position: absolute; left: 44px; top: 56px; width: 312px;
    font-size: 34px; color: var(--brand-teal);
  }
  .front-person { position: absolute; left: 44px; top: 180px; width: 320px; }
  .person-name {
    font-family: "Oswald", sans-serif; font-weight: 700; font-size: 22px;
    color: var(--brand-teal); text-transform: uppercase; letter-spacing: .5px;
  }
  .person-title {
    font-family: "Mulish", sans-serif; font-size: 15px; color: var(--ink-grey);
    margin-top: 2px;
  }
  .contact-list {
    list-style: none; margin-top: 18px;
    font-family: "Mulish", sans-serif; font-size: 15px; color: var(--ink-grey);
  }
  .contact-list li { display: flex; align-items: center; gap: 10px; line-height: 27px; }
  .contact-list svg { width: 15px; height: 15px; flex: none; }
  .contact-address { margin-top: 10px; }
  .chevron-mark {
    position: absolute; right: 44px; bottom: 0;
    width: 230px; height: 270px;
    background: linear-gradient(160deg, var(--brand-teal-light), var(--brand-teal-deep));
  }

  /* Back – landscape */
  .card-back {
    width: 700px; height: 400px;
    background: linear-gradient(135deg, var(--brand-teal-light), var(--brand-teal) 55%, var(--brand-teal-deep));
  }
  .back-pattern {
    position: absolute; inset: 0;
    background: linear-gradient(180deg, rgba(255,255,255,.04), rgba(0,0,0,.06));
  }
  .back-brand {
    position: absolute; inset: 0; display: flex;
    align-items: center; justify-content: center;
    font-size: 36px; color: var(--card-white); text-align: center;
  }
</style>
</head>
<body>
<main class="sheet">
  <section class="card card-front">
    <div class="front-brand brand-name">Rally Functional Fitness</div>
    <div class="front-person">
      <div class="person-name">Dylan Marsh</div>
      <div class="person-title">President/ CEO</div>
      <ul class="contact-list">
        <li>
          <svg viewBox="0 0 16 16" aria-hidden="true"><circle cx="8" cy="8" r="7" fill="none" stroke="#2f8bab" stroke-width="1.3"/><path d="M5.6 4.6l1.3 1.5-.7.9c.5 1 1.3 1.8 2.3 2.3l.9-.7 1.5 1.3-.8 1.2c-2.6-.4-4.9-2.7-5.3-5.3z" fill="#2f8bab"/></svg>
          404.555.0187
        </li>
        <li>
          <svg viewBox="0 0 16 16" aria-hidden="true"><rect x="1.5" y="3.5" width="13" height="9" rx="1" fill="none" stroke="#2f8bab" stroke-width="1.3"/><path d="M1.8 4l6.2 5 6.2-5" fill="none" stroke="#2f8bab" stroke-width="1.3"/></svg>
          info@rallygym.example
        </li>
        <li>
          <svg viewBox="0 0 16 16" aria-hidden="true"><circle cx="8" cy="8" r="6.5" fill="none" stroke="#2f8bab" stroke-width="1.3"/><ellipse cx="8" cy="8" rx="2.8" ry="6.5" fill="none" stroke="#2f8bab" stroke-width="1.1"/><path d="M1.5 8h13" stroke="#2f8bab" stroke-width="1.1"/></svg>
          www.rallygym.example
        </li>
        <li class="contact-address">472 Halvern Drive, Fernvale WK 30041</li>
      </ul>
    </div>
    <div class="chevron-mark" role="img" aria-label="Large brand chevron mark in teal"></div>
  </section>

  <section class="card card-back">
    <div class="back-pattern" role="img" aria-label="Faint repeating chevron pattern in deeper teal"></div>
    <div class="back-brand brand-name">Rally Functional Fitness</div>
  </section>
</main>
</body>
</html>
```